High Tech Real Estate Startup needs a business card

We are developing an innovative real estate marketing product based around advanced search and virtual reality.

We talk to people, we need business cards.

Target Market(s)

The target market is technology professionals and realtors.

Contact Information for Business Card

The information to be included will include

Name
Title
Phone Number
E-mail Address
www.zelquin.com

It should use simple iconography for each one of those fields.

Font styles to use
Other font styles liked:
• Co, Jubilat, Avenir

Colors

Designer to choose colors to be used in the design.

Requirements
Must have
• Clean aesthetic,
• Good use of negative space.
• It should use our company logo, shown in the attached file. It is able to use the negative of that logo (coloured font and white background) and I have attached other acceptable accent colours in a swatch file.
Should not have
• Should not be too busy
• No extraneous text (slogans, tag lines etc)

```html
<!DOCTYPE html>
<html lang="en">
<head>
<meta charset="utf-8">
<title>Zelquin Business Card</title>
<link href="https://fonts.googleapis.com/css2?family=Open+Sans:wght@400;500;600&display=swap" rel="stylesheet">
<style>
  :root {
    --stage: #3b3b3d;
    --card-dark: #252527;
    --front-mark: #1b1b1c;
    --teal: #43b5b7;
    --white: #ffffff;
    --ink-soft: #e6e6e6;
  }
  * { box-sizing: border-box; margin: 0; padding: 0; }
  html, body { width: 799px; height: 1200px; overflow: hidden; }
  body {
    background: var(--stage);
    font-family: "Open Sans", Arial, sans-serif;
    display: flex;
    flex-direction: column;
    align-items: center;
    justify-content: center;
    gap: 120px;
  }
  .card {
    position: relative;
    width: 640px;
    height: 366px;
    border-radius: 26px;
    background: var(--card-dark);
    overflow: hidden;
  }
  .card-front { display: flex; align-items: center; justify-content: center; }
  .front-wordmark {
    font-size: 72px;
    font-weight: 500;
    letter-spacing: 4px;
    color: var(--front-mark);
  }
  .back-wordmark {
    position: absolute;
    left: 40px;
    top: 34px;
    font-size: 50px;
    font-weight: 500;
    letter-spacing: 3px;
    color: var(--teal);
  }
  .contact-list {
    position: absolute;
    left: 40px;
    top: 126px;
    list-style: none;
  }
  .contact-item {
    display: flex;
    align-items: center;
    gap: 10px;
    font-size: 14px;
    color: var(--ink-soft);
    line-height: 22px;
  }
  .contact-icon { width: 14px; height: 14px; flex: none; }
  .wave { position: absolute; inset: 0; width: 100%; height: 100%; }
  .holder {
    position: absolute;
    right: 44px;
    bottom: 42px;
    text-align: right;
    color: var(--white);
  }
  .holder-name { font-size: 23px; font-weight: 600; }
  .holder-title { font-size: 15px; font-weight: 400; margin-top: 2px; }
</style>
</head>
<body>
  <section class="card card-front" aria-label="Card front">
    <span class="front-wordmark">ZELQUIN</span>
  </section>

  <section class="card card-back" aria-label="Card back">
    <svg class="wave" viewBox="0 0 640 366" preserveAspectRatio="none" aria-hidden="true">
      <path fill="var(--teal)" d="M0 190 C120 215 240 300 370 268 C480 240 560 222 640 222 L640 366 L0 366 Z"/>
      <path fill="var(--card-dark)" d="M0 206 C130 235 240 305 370 280 C480 258 560 244 640 240 L640 250 C560 254 480 270 370 294 C230 322 110 262 0 232 Z"/>
      <path fill="var(--card-dark)" d="M0 244 C120 272 230 320 360 302 C450 290 540 275 640 270 L640 274 C540 282 450 298 360 310 C220 328 110 290 0 256 Z"/>
    </svg>

    <span class="back-wordmark">ZELQUIN</span>

    <ul class="contact-list">
      <li class="contact-item">
        <svg class="contact-icon" viewBox="0 0 14 14" aria-hidden="true">
          <circle cx="7" cy="7" r="7" fill="var(--teal)"/>
          <path d="M4.5 3.5 L6 3.5 L6.5 5.5 L5.6 6.2 Q6.5 8 7.8 8.4 L8.5 7.5 L10.5 8 L10.5 9.5 Q7.5 10.5 5 8 Q3.5 6 4.5 3.5 Z" fill="var(--card-dark)"/>
        </svg>
        555.555.5555
      </li>
      <li class="contact-item">
        <svg class="contact-icon" viewBox="0 0 14 14" aria-hidden="true">
          <circle cx="7" cy="7" r="7" fill="var(--teal)"/>
          <rect x="3.5" y="4.5" width="7" height="5" fill="none" stroke="var(--card-dark)" stroke-width="1"/>
          <path d="M3.5 4.5 L7 7.3 L10.5 4.5" fill="none" stroke="var(--card-dark)" stroke-width="1"/>
        </svg>
        alexprice@zelquin.com
      </li>
      <li class="contact-item">
        <svg class="contact-icon" viewBox="0 0 14 14" aria-hidden="true">
          <circle cx="7" cy="7" r="7" fill="var(--teal)"/>
          <circle cx="7" cy="7" r="3.6" fill="none" stroke="var(--card-dark)" stroke-width="0.9"/>
          <path d="M3.4 7 H10.6 M7 3.4 Q5 7 7 10.6 M7 3.4 Q9 7 7 10.6" fill="none" stroke="var(--card-dark)" stroke-width="0.8"/>
        </svg>
        www.zelquin.com
      </li>
    </ul>

    <div class="holder">
      <p class="holder-name">Alex Rowan Price</p>
      <p class="holder-title">Managing Director</p>
    </div>
  </section>
</body>
</html>
```